Working Capital graphics

Our business advisory firm requires 9 images to be re-created and improved in the branding of our business.

The 9 images have been uploaded below and the colours and branding of the business can be found at the website www.tallowmereadvisory.com.au

```html
<!DOCTYPE html>
<html lang="en">
<head>
<meta charset="utf-8">
<title>Payables Drivers</title>
<link rel="stylesheet" href="https://fonts.googleapis.com/css2?family=Jost:wght@500;600;700&display=swap">
<style>
  :root {
    --navy: #1b3784;
    --cyan: #0bb1f5;
    --orange: #f7941d;
    --paper: #ffffff;
    --frame: #d3d3d3;
  }
  html, body {
    margin: 0;
    padding: 0;
    width: 1200px;
    height: 782px;
    overflow: hidden;
    background: var(--frame);
  }
  .canvas {
    display: block;
    width: 1200px;
    height: 782px;
    font-family: "Jost", "Futura", sans-serif;
  }
  .sheet { fill: var(--paper); }
  .page-title { fill: var(--navy); font-size: 53px; font-weight: 700; letter-spacing: 1px; }
  .column-title { fill: var(--navy); font-size: 34px; font-weight: 700; letter-spacing: 1px; }
  .hub-ring { fill: none; stroke: var(--navy); stroke-width: 2.2; }
  .hub-fill { fill: var(--cyan); }
  .hub-label { fill: var(--paper); font-size: 39px; font-weight: 600; letter-spacing: 0.5px; }
  .connector { fill: none; stroke: var(--navy); stroke-width: 2.2; }
  .driver-bar { fill: var(--cyan); }
  .bar-notch { fill: var(--paper); }
  .step-marker { fill: var(--paper); stroke: var(--orange); stroke-width: 2.4; }
  .step-number { fill: var(--navy); font-size: 44px; font-weight: 700; letter-spacing: -1px; }
  .driver-label { fill: var(--paper); font-size: 25px; font-weight: 600; letter-spacing: 1.2px; }
</style>
</head>
<body>
<svg class="canvas" viewBox="0 0 1200 782" xmlns="http://www.w3.org/2000/svg">
  <rect class="sheet" x="7" y="7" width="1186" height="768"/>

  <text class="page-title" x="88" y="109">PAYABLES</text>
  <text class="column-title" x="773" y="113" text-anchor="middle">DRIVERS</text>

  <!-- hub -->
  <circle class="hub-ring" cx="218" cy="445" r="129"/>
  <circle class="hub-fill" cx="218" cy="445" r="117"/>
  <text class="hub-label" x="218" y="441" text-anchor="middle">PAYABLES</text>
  <text class="hub-label" x="218" y="473" text-anchor="middle">DRIVERS</text>

  <!-- connectors -->
  <path class="connector" d="M346 445 H426 M404 214 V675 M404 214 H426 M404 332 H426 M404 558 H426 M404 675 H426"/>

  <!-- driver rows -->
  <g class="driver-row">
    <rect class="driver-bar" x="490" y="183" width="622" height="63" rx="31.5"/>
    <circle class="bar-notch" cx="465.5" cy="214" r="52.5"/>
    <circle class="step-marker" cx="465.5" cy="214" r="39.5"/>
    <text class="step-number" x="465.5" y="230" text-anchor="middle">14</text>
    <text class="driver-label" x="781" y="221" text-anchor="middle">REDUCE EARLY PAYMENTS</text>
  </g>
  <g class="driver-row">
    <rect class="driver-bar" x="490" y="301" width="622" height="63" rx="31.5"/>
    <circle class="bar-notch" cx="465.5" cy="332" r="52.5"/>
    <circle class="step-marker" cx="465.5" cy="332" r="39.5"/>
    <text class="step-number" x="465.5" y="348" text-anchor="middle">15</text>
    <text class="driver-label" x="783" y="341" text-anchor="middle">REDUCE OVER-RIDES</text>
  </g>
  <g class="driver-row">
    <rect class="driver-bar" x="490" y="412" width="622" height="63" rx="31.5"/>
    <circle class="bar-notch" cx="465.5" cy="443" r="52.5"/>
    <circle class="step-marker" cx="465.5" cy="443" r="39.5"/>
    <text class="step-number" x="465.5" y="459" text-anchor="middle">16</text>
    <text class="driver-label" x="781" y="451" text-anchor="middle">REDUCE VENDOR CREDITS</text>
  </g>
  <g class="driver-row">
    <rect class="driver-bar" x="490" y="527" width="622" height="63" rx="31.5"/>
    <circle class="bar-notch" cx="465.5" cy="558" r="52.5"/>
    <circle class="step-marker" cx="465.5" cy="558" r="39.5"/>
    <text class="step-number" x="465.5" y="574" text-anchor="middle">17</text>
    <text class="driver-label" x="788" y="567" text-anchor="middle">INCREASE PO VENDOR TERMS</text>
  </g>
  <g class="driver-row">
    <rect class="driver-bar" x="490" y="644" width="622" height="63" rx="31.5"/>
    <circle class="bar-notch" cx="465.5" cy="675" r="52.5"/>
    <circle class="step-marker" cx="465.5" cy="675" r="39.5"/>
    <text class="step-number" x="465.5" y="691" text-anchor="middle">18</text>
    <text class="driver-label" x="790" y="684" text-anchor="middle">INCREASE INVOICE ONLY TERMS</text>
  </g>
</svg>
</body>
</html>
```